Creative, fresh business card design for Ripplecraft Facades

We need a fresh, creative business card design for Ripplecraft Facades. We are the manufacturer of Ripplecraft Facades in Australia. Wall panels are 2400 x 1200mm panels made from MDF and feature 3D patterns on the face of the panel. The colours to be used are green, silver/grey and white RGB
Red 187
Green 207
Blue 65.

An idea is to possibly use a watermark of one of our designs as a background (like on the "Grids" design on the left hand side of page 2 of our brochure).

Target Market(s)

Interior designers, architects, builders and home renovators

Industry/Entity Type

Business

Contact Information for Business Card

Details to go on the card are:
Our logo (attached),
Slogan: "Decorative panels for interiors and exteriors",
Contact name,
Position,
Mobile phone number,
Business address,
Business phone,
Business fax,
Website and
Email address.

I have attached a few images of our panels and our brochure for reference.

The colours of the business card should feature our logo colours which are: RGB
Red 187
Green 207
Blue 65

Requirements
Must have
• Very modern fonts and design. Some of the designs shown especially the "Prisms" design which is a popular design.
Nice to have
• Creative but simple design. Very contemporary.
Should not have
• Anything ornate or old fashioned.

```html
<!DOCTYPE html>
<html lang="en">
<head>
<meta charset="utf-8">
<title>Ripplecraft Facades – Business Card</title>
<link href="https://fonts.googleapis.com/css2?family=Arimo:wght@700&family=Open+Sans:wght@400&family=Raleway:wght@300;800&display=swap" rel="stylesheet">
<style>
  :root {
    --stage-bg: #d6ccb9;
    --card-dark: #1c1c1c;
    --card-dark-2: #2a2a2a;
    --brand-green: rgb(187, 207, 65);
    --brand-green-deep: #9aa91f;
    --band-grey: #6f6d68;
    --band-text: #e4e2dc;
    --text-light: #c9c7c2;
    --text-muted: #a9a6a0;
    --ink: #1f1f1f;
  }
  * { box-sizing: border-box; margin: 0; padding: 0; }
  html, body {
    width: 1200px; height: 1000px; overflow: hidden;
    background: var(--stage-bg);
  }
  .card {
    position: absolute; left: 420px; top: 85px;
    width: 430px; height: 785px;
    border-radius: 18px; overflow: hidden;
    background: linear-gradient(180deg, var(--card-dark-2), var(--card-dark) 60%);
    font-family: "Open Sans", sans-serif;
  }
  .logo-block {
    position: absolute; left: 0; top: 0; width: 100%; height: 185px;
    background: linear-gradient(180deg, var(--brand-green), var(--brand-green-deep));
    display: flex; align-items: center; justify-content: center;
  }
  .logo-name {
    font-family: "Raleway", sans-serif; font-weight: 800;
    font-size: 62px; letter-spacing: -1px; color: var(--ink);
  }
  .name-band {
    position: absolute; left: 0; top: 190px; width: 100%; height: 68px;
    background: var(--band-grey);
    display: flex; align-items: center; justify-content: center;
    font-family: "Raleway", sans-serif; font-weight: 300;
    font-size: 36px; color: var(--band-text); letter-spacing: -0.5px;
  }
  .slogan {
    position: absolute; left: 0; top: 266px; width: 100%;
    text-align: center; color: var(--brand-green);
    font-size: 17px; line-height: 31px; letter-spacing: 7px;
  }
  .contact-name {
    position: absolute; left: 43px; top: 397px;
    font-family: "Arimo", sans-serif; font-weight: 700;
    font-size: 34px; color: var(--brand-green);
  }
  .contact-role {
    position: absolute; left: 43px; top: 440px;
    font-size: 22px; color: var(--text-light);
  }
  .address {
    position: absolute; left: 43px; top: 487px;
    font-size: 19px; line-height: 24px; color: var(--text-muted);
  }
  .details {
    position: absolute; left: 43px; top: 557px; list-style: none;
  }
  .details li {
    display: flex; align-items: center; height: 29px;
    font-size: 19px; color: var(--text-muted);
  }
  .details svg { width: 18px; height: 18px; margin-right: 12px; fill: var(--brand-green); }
  .details .accent { color: var(--brand-green); }
</style>
</head>
<body>
  <div class="card">
    <div class="logo-block"><span class="logo-name">Ripplecraft</span></div>
    <div class="name-band">Ripplecraft Facades</div>
    <p class="slogan">Decorative Panels for<br>interiors and exteriors</p>

    <h1 class="contact-name">Dana Whitlow</h1>
    <p class="contact-role">Director</p>
    <p class="address">Your Street Address,<br>Harbour City, 1234</p>

    <ul class="details">
      <li><svg viewBox="0 0 18 18" aria-hidden="true"><path d="M5 1h8a1 1 0 0 1 1 1v14a1 1 0 0 1-1 1H5a1 1 0 0 1-1-1V2a1 1 0 0 1 1-1zm1 2v10h6V3zm3 11a1 1 0 1 0 0 2 1 1 0 0 0 0-2z"/></svg>+000 123 456 789</li>
      <li><svg viewBox="0 0 18 18" aria-hidden="true"><path d="M4 1l3 4-2 2c1 2.5 3 4.5 6 6l2-2 4 3-2 3C8 17 1 10 1 3z"/></svg>+000 123 456 789</li>
      <li><svg viewBox="0 0 18 18" aria-hidden="true"><path d="M5 1h7v5H5zM2 7h14v9H2zm9 2v2h3V9zm0 3v2h3v-2zM4 9v6h5V9z"/></svg>+000 123 456 789</li>
      <li><svg viewBox="0 0 18 18" aria-hidden="true"><path d="M1 4h16v11H1zm1.5 1.2L9 10l6.5-4.8z"/></svg>yourname@email.com</li>
      <li><svg viewBox="0 0 18 18" aria-hidden="true"><path d="M10 1a7 7 0 1 1-4.2 12.6L2 17.4 0.6 16l3.8-3.8A7 7 0 0 1 10 1zm0 2.5a4.5 4.5 0 1 0 0 9 4.5 4.5 0 0 0 0-9z"/></svg>www.<span class="accent">websitename</span>.com</li>
    </ul>
  </div>
</body>
</html>
```